job report

Designer – Professional Plumbing Job Report Template

Overview

We are seeking a skilled designer to create a professional, easy-to-use Job Report template for a commercial and maintenance plumbing business.
The report will be used for clients, property managers, facilities managers, strata, and retail centres and must clearly communicate findings, works completed, and recommendations in a polished, compliant, and branded format.

The final document must be suitable for PDF delivery, email, and ongoing reuse.

Objectives

Present plumbing works in a clear, professional, and defensible report format

Improve client understanding of findings and recommendations

Provide a repeatable template that can be used across maintenance, reactive, and investigative works

Allow easy insertion of text, tables, and photos

Report Structure (Minimum Inclusions)
1. Cover Page

Company logo and branding

Report title (e.g. Plumbing Job Report / Investigation Report)

Client name

Site address

Job reference / work order number

Date of attendance

Technician / contractor name

2. Client & Site Details

Client / company name

Site address

Contact person

Contact details

Access notes (after-hours, tenant access, etc.)

3. Reason for Attendance

Clear description of why attendance was required

Call-out type (reactive, scheduled maintenance, investigation, emergency, etc.)

Reported issue or scope requested by client

4. Findings / Observations

Detailed findings discovered on site

Condition of pipework, fixtures, drainage, or systems

Any contributing factors identified

Notes on compliance, wear, damage, or risk

(This section should support bullet points and paragraphs.)

5. Works Carried Out

Step-by-step description of works completed

Equipment used (e.g. jetter, CCTV camera, leak detection, flex shaft, etc.)

Repairs, replacements, testing, and verification

Confirmation that systems were tested and operational on completion

6. Photos & Visual Evidence

Clearly labelled photo sections

Before / during / after photos

Space for photo captions and explanations

Logical layout that aligns photos with written findings

7. Recommendations

Clearly separated from works completed

Urgent vs non-urgent recommendations

Preventative maintenance advice

Upgrade or replacement suggestions

Risk-based language where appropriate

8. Limitations & Exclusions

Areas not inspected

Access limitations

Assumptions made during inspection

Items outside scope of works

9. Conclusion

Summary of outcome

Confirmation of current system status

Next steps (if any)

10. Sign-Off

Contractor / technician name

Company name

Date

Optional client acknowledgement section

Design Requirements

Clean, professional layout

Commercial / trade-appropriate styling (not overly creative)

Easy-to-read fonts

Consistent headings and spacing

Logical flow for busy property managers

Editable format (Word / Google Docs / InDesign source file)

Final export-ready PDF version

Bonus (Nice to Have)

Traffic-light system (Green / Amber / Red) for condition reporting

Iconography for findings, repairs, and recommendations

Optional sections for compliance notes (AS/NCC references)

Space for QR codes or job reference numbers

Deliverables

Editable master report template

PDF version

Instructions or notes for ongoing use

```html
<!DOCTYPE html>
<html lang="en">
<head>
<meta charset="utf-8">
<title>Plumbing Job Report</title>
<link rel="stylesheet" href="https://fonts.googleapis.com/css2?family=Questrial&display=swap">
<style>
  :root {
    --cyan: #52f7fb;
    --yellow: #ffff00;
    --ink: #1c1c1c;
    --paper: #ffffff;
    --rule: #222222;
  }
  * { box-sizing: border-box; margin: 0; padding: 0; }
  html, body { width: 856px; height: 1200px; overflow: hidden; background: var(--paper); }
  body { font-family: "Questrial", "Century Gothic", sans-serif; color: var(--ink); }
  .page { position: relative; width: 856px; height: 1200px; }

  .section-head { position: absolute; left: 52px; width: 753px; height: 22px; }
  .section-head .rule-line { position: absolute; left: 0; right: 0; bottom: 0; height: 2px; background: var(--cyan); }
  .section-head .tab { position: absolute; left: 0; top: 0; bottom: 0; background: var(--cyan); }
  .section-head .flash { position: absolute; top: 0; bottom: 0; width: 73px; background: var(--yellow); clip-path: polygon(0 0, 70% 0, 100% 100%, 30% 100%); }
  .section-head h2 { position: absolute; left: 5px; top: 0; line-height: 22px; font-size: 17.5px; font-weight: 700; letter-spacing: 0.1px; -webkit-text-stroke: 0.35px var(--ink); white-space: nowrap; }

  .field { position: absolute; display: flex; align-items: baseline; font-size: 16.5px; line-height: 18px; white-space: nowrap; }
  .field .fill { flex: 1; margin-left: 6px; border-bottom: 1px solid var(--rule); }
  .rule { position: absolute; left: 52px; width: 753px; border-top: 1px solid var(--rule); }

  .label { position: absolute; left: 52px; font-size: 16.5px; line-height: 18px; white-space: nowrap; }
  .option { position: absolute; border: 1.3px solid var(--rule); font-size: 16px; display: flex; align-items: center; justify-content: center; white-space: nowrap; }

  .photo-col { position: absolute; top: 758px; width: 244px; height: 400px; }
  .photo-col .stage { position: absolute; top: 0; width: 100%; text-align: center; font-size: 16.5px; line-height: 18px; }
  .photo-col .frame { position: absolute; top: 24px; left: 0; width: 244px; height: 180px; border: 1.3px solid var(--rule); background: var(--paper); }
  .photo-col .caption-title { position: absolute; top: 210px; width: 100%; text-align: center; font-size: 16.5px; line-height: 18px; white-space: nowrap; }
  .photo-col .caption-line { position: absolute; left: 0; width: 244px; border-top: 1px solid var(--rule); }
</style>
</head>
<body>
<main class="page">

  <!-- Client & Site Details -->
  <header class="section-head" style="top:51px">
    <div class="rule-line"></div>
    <div class="tab" style="width:197px"></div>
    <div class="flash" style="left:175px"></div>
    <h2>Client &amp; Site Details</h2>
  </header>
  <div class="field" style="top:86px;left:52px;width:393px"><span>Client / Company name:</span><span class="fill"></span></div>
  <div class="field" style="top:86px;left:455px;width:350px"><span>Site address:</span><span class="fill" style="margin-left:10px"></span></div>
  <div class="field" style="top:114px;left:52px;width:393px"><span>Contact person:</span><span class="fill"></span></div>
  <div class="field" style="top:114px;left:455px;width:350px"><span>Contact details:</span><span class="fill" style="margin-left:10px"></span></div>
  <div class="label" style="top:141px">Access notes:</div>
  <div class="option" style="left:177px;top:137px;width:129px;height:26px">After-hours</div>
  <div class="option" style="left:315px;top:137px;width:129px;height:26px">Tenant access</div>
  <div class="field" style="top:141px;left:455px;width:350px"><span>Other:</span><span class="fill"></span></div>

  <!-- Reason for Attendance -->
  <header class="section-head" style="top:183px">
    <div class="rule-line"></div>
    <div class="tab" style="width:224px"></div>
    <div class="flash" style="left:202px"></div>
    <h2>Reason for Attendance</h2>
  </header>
  <div class="field" style="top:216px;left:52px;width:753px"><span>Clear description of why attendance was required:</span><span class="fill"></span></div>
  <div class="label" style="top:245px">Call-out type:</div>
  <div class="option" style="left:197px;top:240px;width:130px;height:26px">Reactive</div>
  <div class="option" style="left:335px;top:240px;width:193px;height:26px">Scheduled maintenance</div>
  <div class="option" style="left:536px;top:240px;width:130px;height:26px">Investigation</div>
  <div class="option" style="left:675px;top:240px;width:130px;height:26px">Emergency</div>
  <div class="field" style="top:273px;left:52px;width:753px"><span>Reported issue or scope requested by client:</span><span class="fill"></span></div>

  <!-- Findings / Observations -->
  <header class="section-head" style="top:307px">
    <div class="rule-line"></div>
    <div class="tab" style="width:224px"></div>
    <div class="flash" style="left:202px"></div>
    <h2>Findings / Observations</h2>
  </header>
  <div class="field" style="top:341px;left:52px;width:753px"><span>• Detailed findings discovered on site:</span><span class="fill"></span></div>
  <div class="rule" style="top:383px"></div>
  <div class="field" style="top:396px;left:52px;width:753px"><span>• Condition of pipework, fixtures, drainage, or systems:</span><span class="fill"></span></div>
  <div class="rule" style="top:439px"></div>
  <div class="field" style="top:453px;left:52px;width:753px"><span>• Any contributing factors identified:</span><span class="fill"></span></div>
  <div class="rule" style="top:495px"></div>
  <div class="field" style="top:508px;left:52px;width:753px"><span>• Notes on compliance, wear, damage, or risk:</span><span class="fill"></span></div>

  <!-- Works Carried Out -->
  <header class="section-head" style="top:542px">
    <div class="rule-line"></div>
    <div class="tab" style="width:191px"></div>
    <div class="flash" style="left:169px"></div>
    <h2>Works Carried Out</h2>
  </header>
  <div class="field" style="top:575px;left:52px;width:753px"><span>Step-by-step description of works completed:</span><span class="fill"></span></div>
  <div class="rule" style="top:617px"></div>
  <div class="label" style="top:631px">Equipment used:</div>
  <div class="option" style="left:197px;top:627px;width:130px;height:26px">Jetter</div>
  <div class="option" style="left:335px;top:627px;width:193px;height:26px">CCTV Camera</div>
  <div class="option" style="left:536px;top:627px;width:130px;height:26px">Leak detection</div>
  <div class="option" style="left:675px;top:627px;width:130px;height:26px">Flex shaft</div>
  <div class="field" style="top:659px;left:52px;width:753px"><span>Repairs, replacements, testing, and verification:</span><span class="fill" style="margin-left:10px"></span></div>
  <div class="field" style="top:687px;left:52px;width:753px"><span>Confirmation that systems were tested and operational on completion:</span><span class="fill" style="margin-left:10px"></span></div>

  <!-- Photos & Visual Evidence -->
  <header class="section-head" style="top:721px">
    <div class="rule-line"></div>
    <div class="tab" style="width:255px"></div>
    <div class="flash" style="left:233px"></div>
    <h2>Photos &amp; Visual Evidence</h2>
  </header>

  <section class="photo-col" style="left:52px">
    <div class="stage">Before</div>
    <div class="frame" role="img" aria-label="Space for before photo"></div>
    <div class="caption-title">Captions and Explanations</div>
    <div class="caption-line" style="top:251px"></div>
    <div class="caption-line" style="top:280px"></div>
    <div class="caption-line" style="top:308px"></div>
    <div class="caption-line" style="top:336px"></div>
    <div class="caption-line" style="top:364px"></div>
    <div class="caption-line" style="top:392px"></div>
  </section>
  <section class="photo-col" style="left:306px">
    <div class="stage">During</div>
    <div class="frame" role="img" aria-label="Space for during photo"></div>
    <div class="caption-title">Captions and Explanations</div>
    <div class="caption-line" style="top:251px"></div>
    <div class="caption-line" style="top:280px"></div>
    <div class="caption-line" style="top:308px"></div>
    <div class="caption-line" style="top:336px"></div>
    <div class="caption-line" style="top:364px"></div>
    <div class="caption-line" style="top:392px"></div>
  </section>
  <section class="photo-col" style="left:561px">
    <div class="stage">After</div>
    <div class="frame" role="img" aria-label="Space for after photo"></div>
    <div class="caption-title">Captions and Explanations</div>
    <div class="caption-line" style="top:251px"></div>
    <div class="caption-line" style="top:280px"></div>
    <div class="caption-line" style="top:308px"></div>
    <div class="caption-line" style="top:336px"></div>
    <div class="caption-line" style="top:364px"></div>
    <div class="caption-line" style="top:392px"></div>
  </section>

</main>
</body>
</html>
```